Popup Nightclub Grand Opening Flyer

We need to design a flyer for the grand opening of an upscale, exclusive nightclub called "Lantern". The design needs to be chic and exclusive. The background should be black and the text should primarily be white. We like minimalist designs.

Here is the text for the flyer
-
Velvetroll Atlanta Presents

Lantern (LOGO)

A Popup Nightclub Experience
For one night Only

Friday, October 18, 2013
Party begins at 9PM

INVITE ONLY

See invitation for location details
(Velvetroll Atlanta logo)

-
Examples we like

http://cdn4-x.pressfolio-example.com/sites/default/files/styles/image_content_width/hash/3b/fd/2468013579_4421_flyer.jpg?itok=K9rtQw2z

http://files.hubspace-example.net/files/8Hqq-Tr72WWE3kaRbTmcxP5QZK2F396J8nbRw4CKMHfdX2Y7qSEF-MqjxDoNrLY3QCyQJD7npjGaRq3k-Mhx6hqf3MDSWf8r3/2zenSaturdays.jpg

http://morvex-example.com/wp-content/uploads/siteskin/widgetkit/gallery/2zen/2zen-gen_qstay4-01.jpg

Hi All, one thing that we are seeing that we don't like is on over emphasis on the phrase "a popup nightclub experience" please don't make this the largest thing on the flyer

Target Market(s)

Target market is 25-35 year olds who are affluent (rich) and like luxury brands

Requirements
Must have
• Dark Background
Nice to have
• Velvetroll Logo on the bottom
Modern text that isn't curvy
Should not have
• Curved text

```html
<!DOCTYPE html>
<html lang="en">
<head>
<meta charset="utf-8">
<title>Lantern Nightclub – Popup Opening Flyer</title>
<link href="https://fonts.googleapis.com/css2?family=Questrial&family=Roboto+Condensed:wght@300;400;700&family=Barlow:wght@400;600&display=swap" rel="stylesheet">
<style>
  :root {
    --ink: #000000;
    --white: #ffffff;
    --silver: #d9d9d9;
    --silver-dark: #a9a9a9;
    --muted: #bdbdbd;
    --rule: #9a9a9a;
  }
  * { margin: 0; padding: 0; box-sizing: border-box; }
  html, body {
    width: 867px;
    height: 1200px;
    overflow: hidden;
    background: var(--ink);
  }
  .flyer {
    position: relative;
    width: 867px;
    height: 1200px;
    background: var(--ink);
    color: var(--white);
    overflow: hidden;
  }
  .flyer__ornament {
    position: absolute;
    inset: 0;
    background:
      radial-gradient(ellipse 200px 150px at 50% 640px, #2b2421 0%, rgba(0,0,0,0) 100%),
      radial-gradient(ellipse 330px 170px at 50% 250px, #1c1715 0%, rgba(0,0,0,0) 100%),
      radial-gradient(ellipse 380px 160px at 50% 1010px, #181412 0%, rgba(0,0,0,0) 100%);
  }
  .line {
    position: absolute;
    left: 0;
    width: 100%;
    text-align: center;
    font-weight: 400;
  }
  .presenter {
    top: 100px;
    font-family: "Questrial", sans-serif;
    font-size: 31px;
    letter-spacing: 0.5px;
  }
  .presents {
    top: 144px;
    font-family: "Questrial", sans-serif;
    font-size: 24px;
    letter-spacing: 9px;
    padding-left: 9px;
  }
  .venue-mark {
    position: absolute;
    left: 50%;
    top: 200px;
    width: 96px;
    height: 96px;
    margin-left: -48px;
    border-radius: 50%;
    border: 10px solid var(--silver);
  }
  .venue-name {
    top: 328px;
    font-family: "Questrial", sans-serif;
    font-size: 58px;
    line-height: 70px;
    letter-spacing: 10px;
    padding-left: 10px;
  }
  .venue-type {
    top: 404px;
    font-family: "Questrial", sans-serif;
    font-size: 20px;
    letter-spacing: 4px;
    padding-left: 4px;
  }
  .rule {
    position: absolute;
    left: 300px;
    width: 268px;
    height: 2px;
    background: linear-gradient(90deg, rgba(154,154,154,0.5), var(--rule) 50%, rgba(154,154,154,0.5));
  }
  .rule--top { top: 532px; }
  .rule--mid { top: 722px; }
  .rule--bottom { top: 780px; }
  .headline {
    top: 544px;
    font-family: "Roboto Condensed", sans-serif;
    font-weight: 700;
    font-size: 46px;
    line-height: 56px;
    background: linear-gradient(180deg, var(--white) 0%, var(--silver) 50%, var(--silver-dark) 100%);
    -webkit-background-clip: text;
    background-clip: text;
    color: transparent;
  }
  .tagline {
    top: 732px;
    font-family: "Barlow", sans-serif;
    font-size: 26px;
    letter-spacing: 0.5px;
    color: var(--silver);
  }
  .dots {
    position: absolute;
    left: 270px;
    width: 323px;
    border-top: 2px dotted var(--muted);
  }
  .dots--top { top: 852px; }
  .dots--bottom { top: 941px; }
  .date {
    top: 864px;
    font-family: "Roboto Condensed", sans-serif;
    font-weight: 700;
    font-size: 30px;
  }
  .time {
    top: 899px;
    font-family: "Roboto Condensed", sans-serif;
    font-weight: 300;
    font-size: 30px;
  }
  .invite {
    top: 966px;
    font-family: "Barlow", sans-serif;
    font-weight: 600;
    font-size: 20px;
    letter-spacing: 6px;
    padding-left: 6px;
  }
  .location-note {
    top: 1018px;
    font-family: "Barlow", sans-serif;
    font-size: 17px;
    letter-spacing: 1px;
    color: var(--muted);
  }
  .host-mark {
    position: absolute;
    top: 1060px;
    left: 0;
    width: 100%;
    display: flex;
    justify-content: center;
    align-items: center;
    gap: 12px;
  }
  .host-mark__dot {
    width: 30px;
    height: 30px;
    border-radius: 50%;
    border: 2px solid var(--white);
  }
  .host-mark__name {
    font-family: "Questrial", sans-serif;
    font-size: 24px;
    letter-spacing: 3px;
    color: var(--white);
  }
</style>
</head>
<body>
  <main class="flyer">
    <div class="flyer__ornament" role="img" aria-label="Dark, softly glowing petal ornament radiating behind the text"></div>

    <p class="line presenter">Velvetroll Atlanta</p>
    <p class="line presents">Presents</p>

    <div class="venue-mark" aria-hidden="true"></div>
    <h1 class="line venue-name">LANTERN</h1>
    <p class="line venue-type">NIGHTCLUB</p>

    <div class="rule rule--top"></div>
    <h2 class="line headline">A POPUP<br>NIGHTCLUB<br>EXPERIENCE</h2>
    <div class="rule rule--mid"></div>
    <p class="line tagline">For one night only</p>
    <div class="rule rule--bottom"></div>

    <div class="dots dots--top"></div>
    <p class="line date">FRIDAY, OCTOBER 18, 2013</p>
    <p class="line time">PARTY BEGINS AT 9PM</p>
    <div class="dots dots--bottom"></div>

    <p class="line invite">INVITE ONLY</p>
    <p class="line location-note">See invitation for location details</p>

    <div class="host-mark">
      <span class="host-mark__dot" aria-hidden="true"></span>
      <span class="host-mark__name">VELVETROLL ATLANTA</span>
    </div>
  </main>
</body>
</html>
```